Specialist aerospace company requires Powerpoint template

We are a company who delivers specialist engineering and testing services. We would like an updated Powerpoint template - specifically one that will be suitable to use in the production of training materials.
We would therefore like the following included:
-Our logo
-A copyright notice
-The course name (e.g. High Voltage Basics)
-The lesson name (e.g. Safe Clearances)
We wish to convey a professional image.

```html
<!DOCTYPE html>
<html lang="en">
<head>
<meta charset="utf-8">
<title>Veltrion Training Template</title>
<link rel="stylesheet" href="https://fonts.googleapis.com/css2?family=Poppins:wght@400;500;600;700;800&display=swap">
<style>
:root{
  --blue:#44739f;
  --blue-text:#3f6f9c;
  --ink:#3b4a5a;
  --dark:#1f2328;
  --body:#3a3f45;
  --pale:#eef2f6;
  --page:#ffffff;
}
*{box-sizing:border-box;margin:0;padding:0}
html,body{width:1200px;height:1111px;overflow:hidden;background:var(--page)}
body{position:relative;font-family:'Poppins',sans-serif;color:var(--body)}
.slide{position:absolute;width:509px;height:286px;background:#fff;overflow:hidden;box-shadow:0 4px 18px rgba(40,55,75,.14)}
.s1{left:70px;top:77px;background:linear-gradient(135deg,#e9eef3 0%,#f4f6f9 55%,#fbfcfd 100%)}
.s2{left:619px;top:77px}
.s3{left:70px;top:408px}
.s4{left:619px;top:408px}
.s5{left:70px;top:739px}
.s6{left:619px;top:739px}
.brand{display:flex;align-items:center;gap:8px;font-weight:600;color:var(--ink);letter-spacing:-.5px}
.brand-mark{background:var(--blue);border-radius:3px}
.title-brand{position:absolute;left:0;right:0;top:56px;justify-content:center;font-size:40px}
.title-brand .brand-mark{width:36px;height:36px}
.title-block{position:absolute;left:0;right:0;text-align:center;color:var(--dark)}
.label{font-size:7.5px;font-weight:500;color:var(--dark)}
.title-block .name{font-size:17px;font-weight:600;line-height:1.2}
.photo{position:absolute}
.heading{font-size:19px;font-weight:600;color:var(--blue-text);line-height:1.2}
.sub-heading{font-size:16.5px;font-weight:600;color:var(--blue-text);line-height:1.25}
.rule{width:62px;height:3px;background:var(--ink);margin-top:6px}
.copy{font-size:9.4px;line-height:15.6px;color:var(--body)}
.text-col{position:absolute}
.footer{position:absolute;left:0;right:0;bottom:0;height:18px;display:flex;align-items:center;background:var(--blue);color:#fff;font-size:6.3px}
.footer .brand{background:#fff;height:18px;width:74px;font-size:9px;gap:3px;padding-left:4px}
.footer .brand-mark{width:8px;height:8px;border-radius:1px}
.footer .item{display:flex;align-items:center;gap:4px;margin-left:9px}
.footer .sep{margin-left:16px;opacity:.6}
.footer .page{margin-left:auto;margin-right:8px}
.footer svg{width:8px;height:8px}
.frame-back{position:absolute;left:14px;top:189px;width:74px;height:58px;background:var(--ink);border-radius:0 0 0 12px}
.framed{position:absolute;left:13px;top:28px;width:210px;height:212px;border:5px solid var(--blue);border-radius:10px;overflow:hidden}
.team-title{position:absolute;left:0;right:0;top:9px;text-align:center}
.team-title .heading{font-size:18px}
.team-title .rule{margin:4px auto 0}
.member{position:absolute;width:139px;height:97px;overflow:hidden}
.member .shade{position:absolute;inset:0;background:linear-gradient(180deg,rgba(0,0,0,0) 45%,rgba(20,24,30,.75) 100%)}
.member .who{position:absolute;left:10px;bottom:3px;color:#fff;line-height:1.1}
.member .who b{display:block;font-size:7px;font-weight:400}
.member .who span{font-size:5px}
.member .social{position:absolute;right:4px;bottom:0;width:13px;height:13px;background:#1d6bb0}
.end-brand{position:absolute;left:0;right:0;top:42px;justify-content:center;font-size:56px;gap:14px}
.end-brand .brand-mark{width:58px;height:58px;border-radius:5px}
.thanks{position:absolute;left:0;right:0;top:143px;text-align:center;font-size:28px;font-weight:800;color:var(--ink);letter-spacing:.5px}
.contact-band{position:absolute;left:35px;top:211px;width:438px;height:50px;background:var(--blue);display:flex;align-items:center;color:#fff;padding-left:29px}
.contact{display:flex;align-items:center;gap:8px;width:142px}
.contact .icon{width:27px;height:27px;border:1.3px solid #fff;display:flex;align-items:center;justify-content:center}
.contact .icon svg{width:13px;height:13px}
.contact b{display:block;font-size:10px;font-weight:600}
.contact span{font-size:7px}
</style>
</head>
<body>
<svg width="0" height="0" style="position:absolute">
  <defs>
    <symbol id="i-globe" viewBox="0 0 16 16"><g fill="none" stroke="#fff" stroke-width="1.2"><circle cx="8" cy="8" r="6.5"/><ellipse cx="8" cy="8" rx="3" ry="6.5"/><path d="M1.5 8h13M2.5 4.8h11M2.5 11.2h11"/></g></symbol>
    <symbol id="i-mail" viewBox="0 0 16 16"><g fill="none" stroke="#fff" stroke-width="1.2"><rect x="1.5" y="3.5" width="13" height="9"/><path d="M1.5 3.5 8 9l6.5-5.5"/></g></symbol>
    <symbol id="i-phone" viewBox="0 0 16 16"><path fill="#fff" d="M4.2 1.5 6.4 4 5.2 5.8c.8 1.8 2.2 3.2 4 4l1.8-1.2 2.5 2.2-1.3 2.2c-5 .2-10.2-5-10-10z"/></symbol>
  </defs>
</svg>

<!-- Title slide -->
<section class="slide s1">
  <div class="brand title-brand"><span class="brand-mark"></span>Veltrion</div>
  <div class="title-block" style="top:145px"><p class="label">The course name</p><p class="name">High Voltage Basics</p></div>
  <div class="title-block" style="top:201px"><p class="label">The lesson name</p><p class="name">Safe Clearances</p></div>
</section>

<!-- About us -->
<section class="slide s2">
  <div class="frame-back"></div>
  <div class="photo" role="img" aria-label="Two technicians reviewing data on a monitor in a lab" style="left:21px;top:38px;width:218px;height:204px;background:linear-gradient(135deg,#d7dfe7,#6f8599 55%,#2f3f52)"></div>
  <div class="text-col" style="left:264px;top:50px;width:236px">
    <h2 class="heading">About Us</h2>
    <div class="rule"></div>
    <p class="copy" style="margin-top:13px">Kapsum dolorsit adfhmetcon ectetur adipiscing elit, sed do eiusmod tempor incididunt ulabore etdolore magna aliquat enim ad minim veniam, quis nostrud exercitation ullamco laboris nisi ut aliquip exeacom odo consequat. Duis aute irure dolor inreprehenderit in voluptate</p>
  </div>
  <footer class="footer">
    <div class="brand"><span class="brand-mark"></span>Veltrion</div>
    <span class="item"><svg><use href="#i-globe"/></svg>www.veltrionhv.com</span><span class="sep">|</span>
    <span class="item"><svg><use href="#i-mail"/></svg>info@veltrionhv.com</span><span class="sep">|</span>
    <span class="item"><svg><use href="#i-phone"/></svg>+1 (555) 014 2290</span>
    <span class="page">Page 02</span>
  </footer>
</section>

<!-- Course slide -->
<section class="slide s3">
  <div class="text-col" style="left:29px;top:46px;width:234px">
    <p class="label">The course name</p>
    <h2 class="sub-heading">High Voltage Basics</h2>
    <div class="rule" style="margin-top:8px"></div>
    <p class="copy" style="margin-top:11px">Kapsum dolorsit adfhmetcon ectetur adipiscing elit, sed do eiusmod tempor incididunt ulabore etdolore magna aliquat enim ad minim veniam, quis nostrud exercitation ullamco laboris nisi ut aliquip exeacom odo consequat. Duis aute irure dolor inreprehenderit in voluptate</p>
  </div>
  <div class="photo" role="img" aria-label="Engineer in hard hat holding a laptop beside industrial robotics" style="left:274px;top:0;width:235px;height:268px;background:linear-gradient(150deg,#e6e9ec,#8aa3b3 45%,#4f7188 70%,#c9764a)"></div>
  <footer class="footer">
    <div class="brand"><span class="brand-mark"></span>Veltrion</div>
    <span class="item"><svg><use href="#i-globe"/></svg>www.veltrionhv.com</span><span class="sep">|</span>
    <span class="item"><svg><use href="#i-mail"/></svg>info@veltrionhv.com</span><span class="sep">|</span>
    <span class="item"><svg><use href="#i-phone"/></svg>+1 (555) 014 2290</span>
    <span class="page">Page 03</span>
  </footer>
</section>

<!-- Lesson slide -->
<section class="slide s4">
  <div class="framed"><div role="img" aria-label="Two engineers in hard hats checking a laptop and test device in a hangar" style="width:100%;height:100%;background:linear-gradient(160deg,#c9ced3,#7b8894 45%,#2a3448)"></div></div>
  <div class="text-col" style="left:254px;top:64px;width:236px">
    <p class="label">The lesson name</p>
    <h2 class="sub-heading">Safe Clearances</h2>
    <div class="rule" style="margin-top:8px"></div>
    <p class="copy" style="margin-top:11px">Kapsum dolorsit adfhmetcon ectetur adipiscing elit, sed do eiusmod tempor incididunt ulabore etdolore magna aliquat enim ad minim veniam, quis nostrud exercitation ullamco laboris nisi ut aliquip exeacom odo consequat. Duis aute irure dolor inreprehenderit in voluptate</p>
  </div>
  <footer class="footer">
    <div class="brand"><span class="brand-mark"></span>Veltrion</div>
    <span class="item"><svg><use href="#i-globe"/></svg>www.veltrionhv.com</span><span class="sep">|</span>
    <span class="item"><svg><use href="#i-mail"/></svg>info@veltrionhv.com</span><span class="sep">|</span>
    <span class="item"><svg><use href="#i-phone"/></svg>+1 (555) 014 2290</span>
    <span class="page">Page 05</span>
  </footer>
</section>

<!-- Team slide -->
<section class="slide s5">
  <div class="team-title"><h2 class="heading">Meet the our team</h2><div class="rule"></div></div>
  <div class="member" style="left:29px;top:44px"><div role="img" aria-label="Portrait of team member" style="position:absolute;inset:0;background:linear-gradient(180deg,#a9b1b6,#5d666d)"></div><div class="shade"></div><div class="who"><b>Marten Leclair</b><span>CEO</span></div><span class="social"></span></div>
  <div class="member" style="left:185px;top:44px"><div role="img" aria-label="Portrait of team member" style="position:absolute;inset:0;background:linear-gradient(180deg,#d6d8da,#6d7278)"></div><div class="shade"></div><div class="who"><b>Dana Okafor</b><span>Employee</span></div><span class="social"></span></div>
  <div class="member" style="left:341px;top:44px"><div role="img" aria-label="Portrait of team member" style="position:absolute;inset:0;background:linear-gradient(180deg,#dfe3e6,#7d858c)"></div><div class="shade"></div><div class="who"><b>Ruben Falke</b><span>Employee</span></div><span class="social"></span></div>
  <div class="member" style="left:29px;top:152px"><div role="img" aria-label="Portrait of team member" style="position:absolute;inset:0;background:linear-gradient(180deg,#e2e5e7,#55606b)"></div><div class="shade"></div><div class="who"><b>Conrad Weiss</b><span>Senior Employee</span></div><span class="social"></span></div>
  <div class="member" style="left:185px;top:152px"><div role="img" aria-label="Portrait of team member" style="position:absolute;inset:0;background:linear-gradient(180deg,#e6e7e8,#5a5d61)"></div><div class="shade"></div><div class="who"><b>Lena Marquez</b><span>Senior Employee</span></div><span class="social"></span></div>
  <div class="member" style="left:341px;top:152px"><div role="img" aria-label="Portrait of team member" style="position:absolute;inset:0;background:linear-gradient(180deg,#eceded,#6b6e72)"></div><div class="shade"></div><div class="who"><b>Sofia Lindqvist</b><span>Senior Employee</span></div><span class="social"></span></div>
  <footer class="footer">
    <div class="brand"><span class="brand-mark"></span>Veltrion</div>
    <span class="item"><svg><use href="#i-globe"/></svg>www.veltrionhv.com</span><span class="sep">|</span>
    <span class="item"><svg><use href="#i-mail"/></svg>info@veltrionhv.com</span><span class="sep">|</span>
    <span class="item"><svg><use href="#i-phone"/></svg>+1 (555) 014 2290</span>
    <span class="page">Page 05</span>
  </footer>
</section>

<!-- Closing slide -->
<section class="slide s6">
  <div class="brand end-brand"><span class="brand-mark"></span>Veltrion</div>
  <p class="thanks">THANK YOU</p>
  <div class="contact-band">
    <div class="contact"><span class="icon"><svg><use href="#i-globe"/></svg></span><div><b>Website</b><span>www.veltrionhv.com</span></div></div>
    <div class="contact"><span class="icon"><svg><use href="#i-phone"/></svg></span><div><b>Call Us</b><span>+1 (555) 014 2290</span></div></div>
    <div class="contact"><span class="icon"><svg><use href="#i-mail"/></svg></span><div><b>Email</b><span>info@veltrionhv.com</span></div></div>
  </div>
</section>
</body>
</html>
```